Tutoring center for k-12 and adults. ( name: Birch Tutoring )

We will start a tutoring center mainly teaching international students English, math, test prep ( SAT,ACT) for K-12 and English conversation class and English grammar for adults. Our mission and description is well described in the attached file below.
Our center is located in Ann Arbor Michigan, and will provide highly qualified instructors.
Our motto is " school like a home and teacher like parents" and "Birch Tutoring is the passage to success" and "Learn to think" I want you to have these main themes as designing the website, and we already have a designed logo attached below in the file. As the name shows, greenish, fresh feeling, but academically informative design is strongly recommended.
I want to emphasize warm and caring atmosphere of our center with the images fitting to this concept.

Target Market(s)

international students (k-12) and adults for ESL classes / high school students both American and international students for test preps: ACT,SAT

Industry/Entity Type

Education

Coding

Number of Pages Required

3 page

Font styles to use
Serif
Sans Serif
Script

Requirements
Must have
• I think there are many options in my website to create different things, but at this point, I just want to make four headings on the top- Home, About us, Classes, Support.
• Home page includes mission statement, testimonial, brief introduction of Test prep classes (SAT,ACT), academic tutoring, and adults classes. Also logo and contact info should be located in the first page. As a second page (heading), classes need to be introduced. I wonder if I can insert Korean for Korean classes. In this section, I want to put class descriptions of each class. As a third heading, About us includes introduction of instructors with their educational background, and please make two more open spots for instructors because we will add more faculties later.
• As the last heading, Support is the section for Q &A and provide the address and map of the center. This part is optional if I go with 3 pages of website!
• It should be informative and simple, easy to find the necessary info.
• If I can update the info by semester or periodically by myself. If it's easy to aces to change and manage the info for me, it will be great.
Nice to have
• .
• If I can have an option to convert the language of the website from English to Korean or to Chinese, it will be very nice.
Should not have
• lesson fees

```html
<!DOCTYPE html>
<html lang="en">
<head>
<meta charset="utf-8">
<title>Birch Tutoring</title>
<link rel="stylesheet" href="https://fonts.googleapis.com/css2?family=Aleo:wght@400;700&family=Open+Sans:wght@400;600&display=swap">
<style>
  :root {
    --lime: #8cc63e;
    --lime-soft: #c9e59a;
    --lime-pale: #eaf5d8;
    --navy: #1d3f6e;
    --ink: #1c1c1c;
    --paper: #ffffff;
    --teal: #3f8c8e;
    --wood: #b0793c;
    --photo-warm: #c9a47c;
  }
  * { margin: 0; padding: 0; box-sizing: border-box; }
  html, body { width: 1200px; height: 2510px; overflow: hidden; background: var(--paper); }
  body { position: relative; font-family: "Aleo", Georgia, serif; color: var(--ink); }
  .abs { position: absolute; }

  .wash-top {
    left: 0; top: 0; width: 1200px; height: 340px;
    background:
      radial-gradient(ellipse 380px 220px at 0 0, var(--lime) 0%, var(--lime-soft) 55%, transparent 75%),
      radial-gradient(ellipse 380px 240px at 100% 0, var(--lime) 0%, var(--lime-soft) 55%, transparent 75%),
      linear-gradient(to bottom, var(--lime-soft) 0%, var(--lime-pale) 22%, rgba(255,255,255,0) 45%);
  }
  .wash-bottom {
    left: 0; top: 2150px; width: 1200px; height: 360px;
    background:
      radial-gradient(ellipse 300px 260px at 0 100%, var(--lime) 0%, var(--lime-soft) 55%, transparent 78%),
      radial-gradient(ellipse 300px 260px at 100% 100%, var(--lime) 0%, var(--lime-soft) 55%, transparent 78%),
      linear-gradient(to top, var(--lime) 0%, var(--lime-soft) 35%, rgba(255,255,255,0) 75%);
  }

  .brand-name { left: 0; width: 1200px; top: 278px; text-align: center;
    font-size: 30px; font-weight: 700; color: var(--navy); }

  .main-nav { top: 336px; left: 0; width: 1200px; }
  .main-nav a {
    position: absolute; transform: translateX(-50%);
    font-family: "Open Sans", Arial, sans-serif; font-size: 14px; color: var(--ink);
    text-decoration: none; letter-spacing: .3px;
  }
  .main-nav a.is-active { color: var(--lime); }

  .mission { font-size: 13.5px; line-height: 26.5px; color: var(--navy); }
  .mission-left { left: 177px; top: 420px; width: 275px; }
  .mission-right { left: 752px; top: 420px; width: 274px; text-align: right; }
  .mission-image { left: 460px; top: 402px; width: 302px; height: 300px;
    background: linear-gradient(180deg, #f2c84b 0%, #d9463a 30%, #4d8fb8 55%, #e7e3d8 80%, #f5f5f5 100%); }

  .section-title { font-family: "Aleo", Georgia, serif; font-weight: 700; color: var(--ink); letter-spacing: .5px; }
  .about-title { left: 0; width: 1200px; top: 708px; text-align: center; font-size: 30px; }
  .about-text { left: 0; width: 1200px; top: 766px; text-align: center;
    font-family: "Open Sans", Arial, sans-serif; font-size: 17.5px; line-height: 25px; color: var(--ink); }

  .class-title { font-size: 29px; line-height: 36px; }
  .class-body { font-size: 17px; line-height: 20.3px; }
  .testprep-title { left: 177px; top: 906px; }
  .testprep-body { left: 177px; top: 1031px; width: 185px; }
  .class-photo { left: 390px; top: 914px; width: 417px; height: 623px;
    background: linear-gradient(160deg, #e8b96a 0%, var(--photo-warm) 35%, #d9d7d2 70%, #eeeeee 100%);
    box-shadow: 0 6px 14px rgba(0,0,0,.35); }
  .splash { left: 803px; top: 837px; width: 397px; height: 690px;
    background: radial-gradient(ellipse at 55% 50%, var(--lime-soft) 0%, var(--lime-pale) 50%, rgba(255,255,255,0) 75%); }
  .tutoring-title { left: 859px; top: 906px; }
  .tutoring-body { left: 861px; top: 1024px; width: 170px; font-size: 13.5px; line-height: 19.7px; }
  .adults-title { left: 863px; top: 1276px; }
  .adults-body { left: 863px; top: 1376px; width: 170px; font-size: 13.5px; line-height: 19.7px; }

  .lime-art { left: 251px; top: 1565px; width: 620px; height: 318px;
    background: radial-gradient(ellipse at 50% 50%, var(--lime-soft) 0%, var(--lime-pale) 55%, rgba(255,255,255,0) 75%); }
  .study-photo { left: 497px; top: 1599px; width: 218px; height: 204px;
    background: linear-gradient(180deg, var(--teal) 0%, #4f9a9b 45%, var(--wood) 75%, #8a5a2b 100%); }
  .extra-body { left: 872px; top: 1592px; width: 155px; text-align: right; font-size: 17px; line-height: 23px; }

  .testimonial-title { left: 177px; top: 1876px; font-size: 29px; }
  .testimonial-quote { left: 177px; top: 1918px; width: 850px; font-size: 17.5px; line-height: 22.6px; color: var(--navy); }
  .slider-arrow { top: 1999px; }
  .slider-prev { left: 124px; }
  .slider-next { left: 1064px; }

  .contact-title { left: 0; width: 1200px; top: 2160px; text-align: center; font-size: 30px; }
  .contact-text { left: 0; width: 1200px; top: 2228px; text-align: center;
    font-family: "Open Sans", Arial, sans-serif; font-size: 16.5px; line-height: 25px; }
</style>
</head>
<body>
  <div class="abs wash-top" role="img" aria-label="Green watercolour border with lime slices and leaves"></div>
  <div class="abs wash-bottom" role="img" aria-label="Green watercolour border with lime slices and leaves"></div>

  <header class="abs brand-name">Birch Tutoring</header>

  <nav class="abs main-nav">
    <a class="is-active" href="#" style="left:413px">HOME</a>
    <a href="#" style="left:539px">ABOUT US</a>
    <a href="#" style="left:653px">CLASSES</a>
    <a href="#" style="left:775px">SUPPORT</a>
  </nav>

  <p class="abs mission mission-left">We are highly motivated to stimulate student's ability to get the best of their ability in academic field. Our teachers are experienced in teaching K-12 students through adult students. Especially, they will help students to improve student's academic qualifications and performance and to enhance possibilities for admission into colleges and universities in the United States.</p>
  <div class="abs mission-image" role="img" aria-label="Stack of colourful books"></div>
  <p class="abs mission mission-right">Also, the bilingual teachers are familiar with Korean curriculums for subjects, so they can prepare the students for return to school in Korea when their parents and they reach the end of their authorized time in the United States.<br>We will provide personal and intimate care for each student to advance their academic ability and motivate them to pursue their goals.</p>

  <h2 class="abs section-title about-title">ABOUT US</h2>
  <p class="abs about-text">We are located in Ann Arbor, one of the hub cities of American education.<br>We provide a highly qualified and selective education to lead our<br>students to a passage of success</p>

  <div class="abs splash" role="img" aria-label="Splash of water with lime slices and leaves"></div>

  <h3 class="abs section-title class-title testprep-title">TEST PREP<br>CLASSES</h3>
  <p class="abs class-body testprep-body">Id eos dicat nonumes, vix elit praesent intellegat ad. Mei at senserit maluisset, has quidam docendi consectetuer ut, sea cu amet quot molestie. Evertitur instructior in vis, sed odio dolorum inciderint id, est at nostrum legendos indoctum.<br><br>Cibo meliore sit cu, ex odio laudem forensibus sit. Vivendo dissentiet at mei, eius veniam tincidunt has in.<br>Id eos dicat nonumes, vix elit praesent intellegat ad. Mei at senserit maluisset, has quidam docendi consectetuer ut, sea cu amet quot molestie. veniam</p>

  <div class="abs class-photo" role="img" aria-label="Photo of a young student reading a book"></div>

  <h3 class="abs section-title class-title tutoring-title">ACADEMIC<br>TUTORING</h3>
  <p class="abs class-body tutoring-body">Id eos dicat nonumes, vix elit praesent intellegat ad. Mei at senserit maluisset, has quidam docendi consectetuer ut, sea cu amet quot molestie. Evertitur instructior in vis, sed odio dolorum inciderint id, est at nostrum legendos indoctum. Cibo meliore sit cu, ex odio laudem forensibus sit. Vivendo</p>

  <h3 class="abs section-title class-title adults-title">ADULTS<br>CLASSES</h3>
  <p class="abs class-body adults-body">Id eos dicat nonumes, vix elit praesent intellegat ad. Mei at senserit maluisset, has quidam docendi consectetuer ut, sea cu amet quot molestie. Evertitur instructior in vis, sed odio dolorum inciderint id, est at nostrum legendos</p>

  <div class="abs lime-art" role="img" aria-label="Watercolour illustration of lime slices and leaves"></div>
  <div class="abs study-photo" role="img" aria-label="Photo of a teacup on a stack of old books"></div>
  <p class="abs class-body extra-body">Tincidunt has in. Id eos dicat nonumes, vix elit praesent intellegat ad. Mei at senserit maluisset, has quidam docendi consectetuer ut, sea cu amet quot molestie. veniam</p>

  <h2 class="abs section-title testimonial-title">TESTIMONIAL</h2>
  <svg class="abs slider-arrow slider-prev" width="20" height="30" viewBox="0 0 20 30" aria-hidden="true"><polygon points="20,0 20,30 0,15" fill="var(--lime)"/></svg>
  <p class="abs testimonial-quote">Ha-eun Park is my great tutor. I have learned English from scratch for about two years from her. She is the best if you want to learn English. Meanwhile my English improved amazingly. She won't give you the fish caught by she will teach you how to catch the fish. Surely she will make your basics of English very solid, so you are absolutely able to use English fully little by little. I believe, if you meet her, it would be a blessing for you.</p>
  <svg class="abs slider-arrow slider-next" width="20" height="30" viewBox="0 0 20 30" aria-hidden="true"><polygon points="0,0 0,30 20,15" fill="var(--lime)"/></svg>

  <h2 class="abs section-title contact-title">CONTACT</h2>
  <p class="abs contact-text">Lorem ipsum dolor sit amet, no duo doming audire. Ut congue<br>posidonium mel, nominavi incorrupte mei et. Ea vim principes<br>conceptam delicatissimi, eu idque nullam graecis eum</p>
</body>
</html>
```